Postcard Design

We need a postcard design for a private lender in the Denver area. We are offering hard money loans and loans for those doing fix-and-flips. We definitely want something that is Colorado-specific, maybe a view of downtown Denver? We are not offering small personal loans, but we are also not lending over 800k. Our audience is not major corporations. all the info in the old postcard is correct EXCEPT:

the new email should be marlowe417@quillnet.example

We would like to omit all use of exclamation points.

```html
<!DOCTYPE html>
<html lang="en">
<head>
<meta charset="utf-8">
<title>Kestrel Lending Co. – Hard Money Loans Postcard</title>
<link rel="stylesheet" href="https://fonts.googleapis.com/css2?family=Barlow+Condensed:wght@300;400;600&family=Oswald:wght@500&family=Open+Sans:wght@400;700&family=Arimo:wght@400&display=swap">
<style>
  :root {
    --backdrop: #2b2f36;
    --paper: #ffffff;
    --teal: #2192b8;
    --title-teal: #2a8fb3;
    --band-light: #a9cfe1;
    --deep-blue: #0a3a94;
    --bright-blue: #00aeef;
    --edge-blue: #1d4fa8;
    --yellow: #fff200;
    --ink: #1f3a4a;
    --green: #76bc43;
    --cyan: #00aeef;
    --orange: #fbad1c;
  }
  * { margin: 0; padding: 0; box-sizing: border-box; }
  html, body { width: 1200px; height: 1200px; overflow: hidden; background: var(--backdrop); }
  .canvas { position: relative; width: 1200px; height: 1200px; }
  .card { position: absolute; left: 280px; width: 640px; height: 494px; background: var(--paper); overflow: hidden; }
  .card--front { top: 100px; }
  .card--back { top: 605px; }

  .brand-title { position: absolute; top: 0; left: 0; width: 100%; height: 94px; display: flex; align-items: center; justify-content: center;
    font-family: "Barlow Condensed", sans-serif; font-weight: 600; font-size: 42px; color: var(--title-teal); }
  .offer-band { position: absolute; top: 94px; left: 0; width: 100%; height: 306px;
    background: linear-gradient(90deg, #ffffff 0%, #ffffff 58%, var(--band-light) 88%, var(--band-light) 100%); }
  .offer-arrow { position: absolute; top: 10px; left: 0; width: 400px; height: 286px; }
  .offer-headline { position: absolute; top: 10px; left: 0; width: 366px; text-align: center; color: #fff; font-family: "Arimo", sans-serif; }
  .offer-headline .hard { position: absolute; top: 32px; left: 0; width: 100%; font-size: 56px; line-height: 1; }
  .offer-headline .money { position: absolute; top: 95px; left: 0; width: 100%; font-size: 80px; line-height: 1; color: var(--yellow); }
  .offer-headline .loans { position: absolute; top: 175px; left: 0; width: 100%; font-size: 56px; line-height: 1; }
  .offer-headline .tagline { position: absolute; top: 250px; left: 0; width: 100%; font-family: "Barlow Condensed", sans-serif; font-weight: 600; font-size: 23px; line-height: 1; }

  .offer-points { position: absolute; top: 50px; left: 392px; width: 240px; list-style: none;
    font-family: "Barlow Condensed", sans-serif; font-weight: 300; font-size: 17px; line-height: 30.4px; color: var(--ink); }
  .offer-points li { position: relative; padding-left: 20px; }
  .offer-points li::before { content: ""; position: absolute; left: 2px; top: 13px; width: 6px; height: 6px; border-radius: 50%; background: var(--ink); }

  .contact-bar { position: absolute; top: 400px; left: 0; width: 100%; height: 94px; background: var(--teal); color: #fff; }
  .contact-call { position: absolute; top: 18px; left: 38px; width: 280px; text-align: center; font-family: "Open Sans", sans-serif; }
  .contact-call .lead { font-size: 18px; line-height: 26px; }
  .contact-call .phone-line { font-size: 21px; font-weight: 700; line-height: 30px; }
  .contact-call .phone { color: var(--yellow); }
  .contact-web { position: absolute; top: 22px; left: 392px; font-family: "Barlow Condensed", sans-serif; font-weight: 400; font-size: 18px; line-height: 23px; }

  .mail-panel { position: absolute; top: 0; left: 0; width: 308px; height: 100%; background: var(--teal); }
  .return-address { position: absolute; top: 26px; left: 41px; color: #fff; font-family: "Barlow Condensed", sans-serif; font-size: 18px; line-height: 23px; }
  .return-address .name { font-weight: 600; font-size: 23px; line-height: 27px; }
  .promo-stripes { position: absolute; top: 0; left: 0; width: 308px; height: 494px; }
  .promo-stripes text { font-family: "Oswald", sans-serif; font-weight: 500; fill: #111; }
</style>
</head>
<body>
<div class="canvas">

  <section class="card card--front">
    <h1 class="brand-title">Kestrel Lending Co.</h1>
    <div class="offer-band">
      <svg class="offer-arrow" viewBox="0 0 400 286" aria-hidden="true">
        <defs>
          <linearGradient id="arrowFill" x1="0" y1="0" x2="1" y2="0">
            <stop offset="0" stop-color="#0a3a94"/>
            <stop offset="1" stop-color="#00aeef"/>
          </linearGradient>
        </defs>
        <polygon points="0,0 335,0 390,142 338,286 0,286" fill="#1d4fa8"/>
        <polygon points="0,0 326,0 378,142 328,286 0,286" fill="url(#arrowFill)"/>
      </svg>
      <div class="offer-headline">
        <div class="hard">Hard</div>
        <div class="money">MONEY</div>
        <div class="loans">Loans</div>
        <div class="tagline">Denver Private Money Lender</div>
      </div>
      <ul class="offer-points">
        <li>We do a cariety of real estate secured loans including loans to buy foreclosures, short sales &amp; more.</li>
        <li>Fix &amp; llio Loans at 10%</li>
        <li>No appraisal, processing fees of “junk” fees</li>
      </ul>
    </div>
    <div class="contact-bar">
      <div class="contact-call">
        <p class="lead">Private money for less</p>
        <p class="phone-line">call us at <span class="phone">303-555-0142</span></p>
      </div>
      <div class="contact-web">
        <p>marlowe417@quillnet.example</p>
        <p>www.kestrellending.example</p>
      </div>
    </div>
  </section>

  <section class="card card--back">
    <div class="mail-panel">
      <div class="return-address">
        <p class="name">Kestrel Lending Co.</p>
        <p>2417 Wynkoop Row</p>
        <p>Denver, CO 80202</p>
      </div>
      <svg class="promo-stripes" viewBox="0 0 308 494" aria-label="Low cost hard money real estate loans">
        <polygon points="0,209 308,131 308,181 0,257" fill="#76bc43"/>
        <polygon points="0,257 308,181 308,233 0,309" fill="#00aeef"/>
        <polygon points="0,309 308,233 308,283 0,361" fill="#fbad1c"/>
        <text x="59" y="233" font-size="38" transform="rotate(-14.2 59 233)">LOW COST</text>
        <text x="38" y="293" font-size="40" transform="rotate(-14.2 38 293)">HARD MONEY</text>
        <text x="33" y="339" font-size="33" transform="rotate(-14.2 33 339)">REAL ESTATE LOANS</text>
      </svg>
    </div>
  </section>

</div>
</body>
</html>
```